Tech business card design

We need an amazing business card design for our new business 'Pexla' a marketing tech startup based in Sydney, Australia. We provide an online marketplace for businesses to search and buy advertising media, connect with service providers and learn more about marketing. We wish to communicate 'cool tech', reliability and professionalism and design based around our logo.

Target Market(s)

Business Owners

Contact Information for Business Card

Name
Position
Email Address
Website
Phone Number

Font styles to use
Other font styles liked:
• Avenir & Avenir Next

Colors

Designer to choose colors to be used in the design.

```html
<!DOCTYPE html>
<html lang="en">
<head>
<meta charset="utf-8">
<title>Pexla Business Card</title>
<link href="https://fonts.googleapis.com/css2?family=Nunito+Sans:wght@400;700;900&display=swap" rel="stylesheet">
<style>
  :root {
    --navy: #1b1f4b;
    --navy-soft: #5b5f8c;
    --grey: #8a8b90;
    --white: #ffffff;
    --backdrop: #e9e9ec;
    --ink: #1d1d24;
  }
  * { margin: 0; padding: 0; box-sizing: border-box; }
  html, body { width: 1200px; height: 900px; overflow: hidden; }
  body {
    background: var(--backdrop);
    font-family: "Nunito Sans", Arial, sans-serif;
    position: relative;
  }
  .card {
    position: absolute;
    width: 560px;
    height: 320px;
    border-radius: 22px;
    overflow: hidden;
    box-shadow: 0 10px 30px rgba(0,0,0,0.18);
  }
  .card--front { left: 140px; top: 100px; background: var(--white); }
  .card--back { left: 500px; top: 480px; background: var(--navy); }

  .card__wave { position: absolute; inset: 0; width: 100%; height: 100%; }

  .brand-name {
    position: absolute;
    left: 0; right: 0;
    text-align: center;
    font-weight: 900;
    color: var(--navy);
    letter-spacing: -1px;
    line-height: 1;
  }
  .card--front .brand-name { top: 26px; font-size: 76px; }
  .card--back .brand-name {
    top: 88px;
    font-size: 150px;
    color: var(--navy-soft);
  }

  .person {
    position: absolute;
    left: 0; right: 0;
    top: 116px;
    text-align: center;
    color: var(--ink);
  }
  .person__name { font-size: 18px; font-weight: 900; letter-spacing: 0.5px; }
  .person__role { font-size: 14px; font-weight: 700; margin-top: 1px; }

  .contacts {
    position: absolute;
    left: 0; right: 0;
    top: 164px;
    display: flex;
    justify-content: center;
    gap: 18px;
    font-size: 14px;
    line-height: 18px;
    color: var(--ink);
  }
  .contacts__item { display: flex; align-items: center; gap: 4px; }
  .contacts__icon { width: 12px; height: 12px; fill: var(--ink); }

  .address {
    position: absolute;
    left: 0; right: 0;
    bottom: 24px;
    text-align: center;
    font-size: 14px;
    color: var(--white);
    letter-spacing: 0.3px;
  }
</style>
</head>
<body>

  <section class="card card--front" aria-label="Business card front">
    <svg class="card__wave" viewBox="0 0 560 320" preserveAspectRatio="none" aria-hidden="true">
      <path d="M0,228 C120,273 280,263 380,226 C450,204 510,196 560,192" fill="none" stroke="var(--grey)" stroke-width="5"/>
      <path d="M0,240 C120,285 280,275 380,238 C450,216 510,208 560,204 V320 H0 Z" fill="var(--navy)"/>
      <path d="M0,248 C120,293 280,283 380,246 C450,224 510,216 560,212" fill="none" stroke="var(--white)" stroke-width="1.5"/>
    </svg>

    <div class="brand-name">Pexla</div>

    <div class="person">
      <div class="person__name">JOHN SMITH</div>
      <div class="person__role">Position</div>
    </div>

    <div class="contacts">
      <span class="contacts__item">
        <svg class="contacts__icon" viewBox="0 0 24 24" aria-hidden="true"><path d="M6.6 10.8a15.1 15.1 0 0 0 6.6 6.6l2.2-2.2a1 1 0 0 1 1-.25 11.4 11.4 0 0 0 3.6.57 1 1 0 0 1 1 1V20a1 1 0 0 1-1 1A17 17 0 0 1 3 4a1 1 0 0 1 1-1h3.5a1 1 0 0 1 1 1c0 1.25.2 2.45.57 3.57a1 1 0 0 1-.25 1z"/></svg>
        012-345-6789
      </span>
      <span class="contacts__item">
        <svg class="contacts__icon" viewBox="0 0 24 24" aria-hidden="true"><path d="M2 5h20v14H2z M4 7v.4l8 5 8-5V7l-8 5z" fill-rule="evenodd"/></svg>
        info@pexla.com
      </span>
      <span class="contacts__item">
        <svg class="contacts__icon" viewBox="0 0 24 24" aria-hidden="true"><circle cx="12" cy="12" r="10" fill="none" stroke="var(--ink)" stroke-width="2"/><ellipse cx="12" cy="12" rx="4" ry="10" fill="none" stroke="var(--ink)" stroke-width="1.6"/><path d="M2 12h20M4 7h16M4 17h16" stroke="var(--ink)" stroke-width="1.4"/></svg>
        www.pexla.com
      </span>
    </div>

    <div class="address">Street Name, City Name, Zipcode:012345</div>
  </section>

  <section class="card card--back" aria-label="Business card back">
    <div class="brand-name">Pexla</div>
  </section>

</body>
</html>
```